We need a laundry sheet packingbox desgin

-look at our website lindavel.nl to be in line with our house style/collor
We are a perfume seller and would like to offer also wasshingsheets with NO SMELL, so the customers can buy this incombination with our washingperfumes.
-the wassingheets will be neutrale(NO SMELL)
-it will be for the Dutch market
The next points should be on the desgin of the package
-our brand name: LINDAVEL
-product name: WASSTRIPS
-(contains) Bevat: 30 wasstrips
-30 wasstrips = 60 wasbeurten
Please take some inspiration of others sellers & regarding eco friendly symbols etc.:
voltirra.com & plomkens.nl
Backside information will be provided afther we found the right desgin
Please look at attachement pdf open box.
Here you can find the pdf design where you need to customize:
https://fz.qx/t-kR8bNwL2sY

```html
<!DOCTYPE html>
<html lang="nl">
<head>
<meta charset="UTF-8">
<title>LINDAVEL Wasstrips – verpakking</title>
<link href="https://fonts.googleapis.com/css2?family=Montserrat:wght@400;500&family=Cormorant+Garamond:wght@500&display=swap" rel="stylesheet">
<style>
  :root {
    --backdrop: #dedede;
    --box-black: #1c1c1c;
    --box-black-deep: #141414;
    --gold: #b8903a;
    --gold-light: #d0a94f;
    --gold-dark: #8d6624;
    --white: #f2f2f2;
    --ink: #1a1a1a;
    --line: #4a4a4a;
  }
  * { margin: 0; padding: 0; box-sizing: border-box; }
  html, body { width: 1200px; height: 800px; overflow: hidden; }
  body { background: var(--backdrop); position: relative; font-family: "Montserrat", sans-serif; }

  .package { position: absolute; left: 355px; top: 40px; width: 490px; height: 720px; display: flex; }

  .front-panel {
    position: relative; width: 440px; height: 720px; overflow: hidden;
    background: linear-gradient(90deg, var(--box-black) 0%, var(--box-black) 60%, var(--box-black-deep) 100%);
  }
  .halftone-area {
    position: absolute; right: 0; top: 0; width: 220px; height: 270px;
    background: radial-gradient(ellipse at 80% 35%, rgba(70,70,70,.55) 0%, rgba(45,45,45,.3) 45%, rgba(28,28,28,0) 75%);
  }
  .tear-outline { position: absolute; left: 0; top: 0; width: 440px; height: 720px; }

  .rotated { position: absolute; transform: translate(-50%, -50%) rotate(-90deg); white-space: nowrap; }

  .brand-mark { left: 40%; top: 50%; display: flex; align-items: center; gap: 14px; }
  .brand-mark__dot { width: 18px; height: 18px; border-radius: 50%; background: var(--gold); }
  .brand-mark__name {
    font-family: "Cormorant Garamond", serif; font-weight: 500; font-size: 20px;
    letter-spacing: 1px; color: var(--gold);
  }

  .product-name {
    left: 55.5%; top: 50%;
    font-weight: 500; font-size: 56px; letter-spacing: 9px; color: var(--white);
  }

  .content-badge { left: 84%; top: 50%; display: flex; flex-direction: column; align-items: flex-start; }
  .content-badge__pill {
    display: flex; align-items: stretch; height: 28px;
    border: 2px solid var(--gold); border-radius: 14px; overflow: hidden; background: var(--gold);
  }
  .content-badge__label {
    background: var(--box-black); color: var(--gold); font-size: 17px;
    padding: 0 8px; border-radius: 0 14px 14px 0; line-height: 24px;
  }
  .content-badge__count { color: var(--ink); font-size: 17px; padding: 0 10px 0 6px; line-height: 24px; }
  .content-badge__note {
    margin-left: 14px; background: var(--white); color: var(--ink);
    font-size: 7px; letter-spacing: .6px; padding: 2px 10px 2px 6px; border-radius: 0 0 4px 4px;
  }

  .side-panel {
    position: relative; width: 50px; height: 720px;
    background: linear-gradient(90deg, var(--gold-dark) 0%, var(--gold) 55%, var(--gold-dark) 100%);
  }
  .side-brand { left: 50%; top: 60%; display: flex; align-items: center; gap: 8px; }
  .side-brand__dot { width: 8px; height: 8px; border-radius: 50%; background: var(--ink); }
  .side-brand__name { font-family: "Cormorant Garamond", serif; font-weight: 500; font-size: 9px; letter-spacing: 1px; color: var(--ink); }
</style>
</head>
<body>
  <main class="package">
    <section class="front-panel">
      <div class="halftone-area" role="img" aria-label="Decoratief stippelpatroon in donkergrijs"></div>

      <svg class="tear-outline" viewBox="0 0 440 720" aria-hidden="true">
        <path d="M440 96 L64 96 Q58 96 58 102 L58 612 Q58 618 64 618 L440 618" fill="none" stroke="var(--line)" stroke-width="1"/>
        <line x1="98" y1="101" x2="440" y2="101" stroke="var(--line)" stroke-width="1.2" stroke-dasharray="6 5"/>
        <line x1="98" y1="613" x2="440" y2="613" stroke="var(--line)" stroke-width="1.2" stroke-dasharray="6 5"/>
        <line x1="98" y1="92" x2="98" y2="108" stroke="var(--line)" stroke-width="1"/>
        <line x1="98" y1="606" x2="98" y2="622" stroke="var(--line)" stroke-width="1"/>
      </svg>

      <div class="rotated brand-mark">
        <span class="brand-mark__dot"></span>
        <span class="brand-mark__name">LINDAVEL</span>
      </div>

      <h1 class="rotated product-name">WASSTRIPS</h1>

      <div class="rotated content-badge">
        <div class="content-badge__pill">
          <span class="content-badge__label">Bevat</span>
          <span class="content-badge__count">30 wasstrips</span>
        </div>
        <span class="content-badge__note">30 WASSTRIPS = 60 WASBEURTEN</span>
      </div>
    </section>

    <aside class="side-panel">
      <div class="rotated side-brand">
        <span class="side-brand__dot"></span>
        <span class="side-brand__name">LINDAVEL</span>
      </div>
    </aside>
  </main>
</body>
</html>
```